Termite Mailer September 2021

We need a clean modern looking flyer advertising termites via the mail.

Size should be 9"x6"

Our tagline is "The Smarter Approach to Pest Control"

Something along the stylistic design of these:

https://pics.lumora-share.net/Qk82vLmTzPwX4rNa1

https://pics.lumora-share.net/Hd37nBcYxTqW9sKe5

https://pics.lumora-share.net/Zr61pMfVaLuE2jGo8

https://www.cardvistaprint.net/wp-content/uploads/designs/img/Pest-Prevention-Postcard-PST-1003.jpg

Should include some of this verbiage:

HAVE YOU SCHEDULED YOUR ANNUAL TERMITE INSPECTION? - MAKE IT IN RED

DON'T WAIT. PROTECT YOUR HOME TODAY!

ABSOLUTELY FREE INSPECTION. NO OBLIGATION.

TERMITES CAN CAUSE SEVERE DAMAGE TO YOUR HOME.

BRIMVALE LOGO

THE SMARTER APPROACH TO PEST CONTROL.

PROTECT YOUR MOST VALUABLE ASSET.

10% DISCOUNT ON ANY SERVICE GUARANTEED IF YOU CALL TODAY.

INCLUDE A PICTURE OF A TERMITE AS WELL SOMEWHERE AND WOOD DAMAGE.

Target Market(s)

Homeowners in Southern California USA

Industry/Entity Type

Pest Control/Extermination

Font styles to use
Other font styles liked:
• Chaparral Pro Italic, Brava Slab

Requirements
Must have
• Clean design, picture of house, picture of Termite, 10% off coupon and call to action on the back
Should not have
• Bad looking houses, colors that don't match our logo

```html
<!DOCTYPE html>
<html lang="en">
<head>
<meta charset="utf-8">
<title>Brimvale Pest Control – Termite Mailer</title>
<link href="https://fonts.googleapis.com/css2?family=Enriqueta:wght@700&family=Bitter:wght@700&family=Alegreya:ital,wght@1,400&family=Roboto+Condensed:wght@300&display=swap" rel="stylesheet">
<style>
  :root{
    --backdrop:#595959;
    --paper:#ffffff;
    --brand-blue:#1b6db3;
    --brand-blue-dark:#0f4f8f;
    --brand-green:#7cc242;
    --alert-red:#d3161b;
    --alert-red-dark:#a80f13;
    --wood-light:#b98a72;
    --wood-dark:#6e4030;
  }
  *{margin:0;padding:0;box-sizing:border-box}
  html,body{width:1200px;height:1000px;overflow:hidden;background:var(--backdrop)}
  .stage{position:relative;width:1200px;height:1000px}
  .mailer{position:absolute;left:36px;top:121px;width:1128px;height:758px;background:var(--paper);overflow:hidden}
  .mailer > *{position:absolute}

  .slab{font-family:"Enriqueta",Georgia,serif;font-weight:700}
  .figures{font-family:"Bitter",Georgia,serif;font-weight:700}

  .brand{left:72px;top:38px;display:flex;align-items:center;gap:14px}
  .brand-dot{width:58px;height:58px;border-radius:50%;background:var(--brand-blue)}
  .brand-name{font-size:44px;color:var(--brand-blue);letter-spacing:1px;line-height:1}

  .tagline{left:430px;top:40px;font-family:"Alegreya",Georgia,serif;font-style:italic;font-size:45px;color:var(--brand-blue);white-space:nowrap;letter-spacing:.3px}

  .termite-photo{left:0;top:500px;width:570px;height:258px;
    background:linear-gradient(160deg,var(--wood-light) 0%,#9a6450 45%,var(--wood-dark) 100%)}

  .headline-panel{left:0;top:142px;width:572px;height:373px}
  .headline{left:72px;top:166px;color:#fff;font-size:52px;line-height:60px;letter-spacing:1px;white-space:nowrap}

  .offer-free{left:589px;top:170px;color:var(--brand-green);font-size:30px;line-height:40px;letter-spacing:.5px;white-space:nowrap}
  .offer-discount{left:589px;top:266px;color:var(--brand-blue);white-space:nowrap}
  .offer-discount .big{display:block;font-size:60px;line-height:70px;letter-spacing:1px}
  .offer-discount .thin{display:block;font-family:"Roboto Condensed",Arial,sans-serif;font-weight:300;font-size:36px;line-height:36px;letter-spacing:.5px}
  .offer-discount .call{display:block;font-size:47px;line-height:58px;letter-spacing:.5px}

  .phone-band{left:536px;top:450px;width:592px;height:96px}
  .phone{left:586px;top:459px;color:#fff;font-size:54px;line-height:74px;letter-spacing:1px;white-space:nowrap}

  .protect{left:587px;top:566px;color:var(--brand-green);font-size:29px;line-height:40px;letter-spacing:.5px;white-space:nowrap}

  .web{left:646px;top:684px;display:flex;align-items:center;gap:14px;color:var(--brand-blue);font-size:30px;white-space:nowrap}
</style>
</head>
<body>
<div class="stage">
  <section class="mailer">
    <div class="brand">
      <span class="brand-dot"></span>
      <span class="brand-name slab">BRIMVALE</span>
    </div>
    <p class="tagline">The Smarter Approach to Pest Control</p>

    <div class="termite-photo" role="img" aria-label="Close-up photo of a termite crawling on damaged, eaten wood"></div>

    <svg class="headline-panel" viewBox="0 0 572 373" aria-hidden="true">
      <defs>
        <linearGradient id="redFill" x1="0" y1="0" x2="1" y2="1">
          <stop offset="0" stop-color="var(--alert-red)"/>
          <stop offset="1" stop-color="var(--alert-red-dark)"/>
        </linearGradient>
      </defs>
      <path d="M0 0 H564 Q572 0 570 8 L506 366 Q505 373 498 373 H0 Z" fill="url(#redFill)"/>
    </svg>
    <h1 class="headline slab">HAVE YOU<br>SCHEDULED<br>YOUR ANNUAL<br>TERMITE<br>INSPECTION?</h1>

    <p class="offer-free slab">ABSOLUTELY FREE INSPECTION.<br>NO OBLIGATION.</p>

    <p class="offer-discount">
      <span class="big slab"><span class="figures">10%</span> DISCOUNT</span>
      <span class="thin">ON ANY SERVICE GUARANTEED</span>
      <span class="call slab">IF YOU CALL TODAY</span>
    </p>

    <svg class="phone-band" viewBox="0 0 592 96" aria-hidden="true">
      <defs>
        <linearGradient id="blueFill" x1="0" y1="0" x2="1" y2="0">
          <stop offset="0" stop-color="var(--brand-blue-dark)"/>
          <stop offset="1" stop-color="var(--brand-blue)"/>
        </linearGradient>
      </defs>
      <path d="M20 0 H592 V96 H8 Q0 96 1 88 L13 6 Q14 0 20 0 Z" fill="url(#blueFill)"/>
    </svg>
    <p class="phone figures">+1 714-555-0148</p>

    <p class="protect slab">PROTECT YOUR MOST<br>VALUABLE ASSET.</p>

    <p class="web slab">
      <svg width="28" height="28" viewBox="0 0 28 28" aria-hidden="true" fill="none" stroke="var(--brand-blue)" stroke-width="2">
        <circle cx="14" cy="14" r="12"/>
        <ellipse cx="14" cy="14" rx="5" ry="12"/>
        <path d="M2 14 H26 M4.5 8 H23.5 M4.5 20 H23.5"/>
      </svg>
      www.gobrimvale.com
    </p>
  </section>
</div>
</body>
</html>
```